Business card for Eyelash extension salon in Marlowe Hills,California USA

We need new business card for our salon in Marlowe Hills. The salon name is 'Lashvera' . We would like to have...Business name: Lashvera Name of person: will provide later Address 4720 N.Alder Crest Ave Marlowe Hills , CA 90417 Phone: will provide later (Text only) Web: www.lashverastudio.example Snapgrid icon, Circlebook icon follow us for seasonal campaign and news @lashverastudiolounge Design should look elegant, high-end, clean, simple, cohesive with my brand. Please refer my brand board. Business name color will be metallic bronzy color. Im thinking grey background or white background. Thanks

Target Market(s)

25-35. Gender neutral. People who are in Entertainment business industry.
This is High-end Eyelash extension salon in Marlowe Hills

Industry/Entity Type

Beauty Salon

Contact Information for Business Card

Business name: Lashvera
Name of person: will provide later
Address 4720 N.Alder Crest Ave Marlowe Hills , CA 90417
Phone: will provide later (Text only)
Web: www.lashverastudio.example
Snapgrid icon, Circlebook icon
follow us for seasonal campaign and news @lashverastudiolounge

Requirements
Must have
• Beautiful, elegant, clean and simple look but very attractive and modern
Should not have
• We don't like too clutter, too busy designs.

```html
<!DOCTYPE html>
<html lang="en">
<head>
<meta charset="utf-8">
<title>Lashvera Business Card</title>
<link href="https://fonts.googleapis.com/css2?family=Work+Sans:wght@400;500&family=Playfair+Display:wght@500&display=swap" rel="stylesheet">
<style>
  :root {
    --backdrop: #e7e3de;
    --card: #f4f4f4;
    --bronze: #8a6149;
    --bronze-text: #7d5843;
    --icon-glyph: #f4f4f4;
  }
  * { box-sizing: border-box; margin: 0; padding: 0; }
  html, body { width: 1200px; height: 960px; overflow: hidden; }
  body {
    background: var(--backdrop);
    position: relative;
    font-family: "Work Sans", Arial, sans-serif;
    color: var(--bronze-text);
  }
  .card {
    position: absolute;
    left: 270px;
    width: 664px;
    height: 381px;
    background: var(--card);
    overflow: hidden;
    box-shadow: 0 2px 10px rgba(0,0,0,0.12);
  }
  .card--front { top: 71px; }
  .card--back { top: 509px; }

  .rule { position: absolute; background: var(--bronze); }
  .rule--h { height: 1.5px; }
  .rule--v { width: 1.5px; }

  /* front */
  .brand {
    position: absolute;
    left: 0; right: 0;
    top: 145px;
    text-align: center;
  }
  .brand__name {
    font-size: 68px;
    font-weight: 400;
    letter-spacing: 1px;
    line-height: 1;
    color: var(--bronze);
  }
  .brand__place {
    display: block;
    margin-top: 18px;
    margin-left: 126px;
    font-size: 9px;
    font-weight: 500;
    letter-spacing: 1.6px;
    text-transform: uppercase;
  }
  .social {
    position: absolute;
    right: 51px;
    top: 325px;
    display: flex;
    gap: 16px;
    align-items: center;
    font-size: 15px;
    letter-spacing: 0.6px;
  }
  .social__net { display: flex; align-items: center; gap: 6px; }
  .social__dot { width: 10px; height: 10px; background: var(--bronze); border-radius: 50%; }

  /* back */
  .holder {
    position: absolute;
    right: 44px;
    top: 65px;
    text-align: right;
  }
  .holder__name {
    font-family: "Playfair Display", Georgia, serif;
    font-weight: 500;
    font-size: 20px;
    letter-spacing: 0.5px;
    line-height: 1.2;
    text-transform: uppercase;
  }
  .holder__role {
    font-size: 15px;
    letter-spacing: 2px;
    line-height: 1.2;
    margin-top: 1px;
  }
  .contacts {
    position: absolute;
    left: 15px;
    top: 167px;
    list-style: none;
  }
  .contacts__item {
    display: flex;
    align-items: center;
    height: 22px;
    margin-bottom: 19px;
    font-size: 15px;
    letter-spacing: 0.4px;
  }
  .contacts__icon { width: 22px; height: 22px; margin-right: 30px; flex: none; }
</style>
</head>
<body>

<section class="card card--front" aria-label="Card front">
  <div class="rule rule--h" style="left:0; top:22px; width:605px;"></div>
  <div class="rule rule--v" style="left:32px; top:0; height:266px;"></div>
  <div class="rule rule--v" style="left:635px; top:77px; height:304px;"></div>
  <div class="rule rule--h" style="left:399px; top:355px; width:265px;"></div>

  <div class="brand">
    <div class="brand__name">Lashvera</div>
    <span class="brand__place">Marlowe Hills</span>
  </div>

  <div class="social">
    <span class="social__net"><span class="social__dot"></span>Snapgrid</span>
    <span class="social__net">Circlebook</span>
    <span class="social__handle">@lashvera</span>
  </div>
</section>

<section class="card card--back" aria-label="Card back">
  <div class="rule rule--h" style="left:276px; top:42px; width:388px;"></div>
  <div class="rule rule--v" style="left:640px; top:0; height:280px;"></div>
  <div class="rule rule--v" style="left:52px; top:116px; height:265px;"></div>
  <div class="rule rule--h" style="left:0; top:342px; width:605px;"></div>

  <div class="holder">
    <div class="holder__name">Corinne Vastel</div>
    <div class="holder__role">Manager</div>
  </div>

  <ul class="contacts">
    <li class="contacts__item">
      <svg class="contacts__icon" viewBox="0 0 22 22" aria-hidden="true">
        <circle cx="11" cy="11" r="11" fill="var(--bronze)"/>
        <path d="M11 5.5a3.6 3.6 0 0 0-3.6 3.6c0 2.7 3.6 7 3.6 7s3.6-4.3 3.6-7A3.6 3.6 0 0 0 11 5.5z" fill="var(--icon-glyph)"/>
        <circle cx="11" cy="9.1" r="1.3" fill="var(--bronze)"/>
      </svg>
      4720 N.Alder Crest Ave Marlowe Hills , CA 90417
    </li>
    <li class="contacts__item">
      <svg class="contacts__icon" viewBox="0 0 22 22" aria-hidden="true">
        <circle cx="11" cy="11" r="11" fill="var(--bronze)"/>
        <rect x="7.8" y="5.5" width="6.4" height="11" rx="1.2" fill="none" stroke="var(--icon-glyph)" stroke-width="1.3"/>
        <circle cx="11" cy="14.6" r="0.7" fill="var(--icon-glyph)"/>
      </svg>
      555-014-2286
    </li>
    <li class="contacts__item">
      <svg class="contacts__icon" viewBox="0 0 22 22" aria-hidden="true">
        <circle cx="11" cy="11" r="11" fill="var(--bronze)"/>
        <g fill="none" stroke="var(--icon-glyph)" stroke-width="1">
          <circle cx="11" cy="11" r="4.6"/>
          <ellipse cx="11" cy="11" rx="2" ry="4.6"/>
          <path d="M6.4 11h9.2"/>
        </g>
      </svg>
      lashverastudio.example
    </li>
    <li class="contacts__item">
      <svg class="contacts__icon" viewBox="0 0 22 22" aria-hidden="true">
        <circle cx="11" cy="11" r="11" fill="var(--bronze)"/>
        <rect x="6" y="7.5" width="10" height="7" rx="0.8" fill="none" stroke="var(--icon-glyph)" stroke-width="1.2"/>
        <path d="M6.3 7.9 11 11.4l4.7-3.5" fill="none" stroke="var(--icon-glyph)" stroke-width="1.2"/>
      </svg>
      hello@lashvera.example
    </li>
  </ul>
</section>

</body>
</html>
```